I need a logo that demonstrates multiple of the same with one of a distinguishing feature. I would like something that can be recognisable in silhouette format. The business designs Management systems bespoke the to the company helping them pre-qualify for work.
Something that can demonstrate a distinction between a collective group non of which are the same in shape or size, with the largest of these not the distinguished object (or something to that effect).
This is a new business no logo or artwork exists.
Target Market(s)
Small to Medium Size enterprises in the city and rural areas. Looking to make the step up.
Industry/Entity Type
Manufacture
Contact Information for Business Card
room for, Name, Email, phone number
Font styles to use
Requirements
Must have
- would like the silhouette to be recognisable
Nice to have
- would like it to incorporate the name Keystone Advisory Frameworks.
- Would like the same logo to be on both business cards and on corporate shirts
Should not have
- anything that may exclude rural trade or manufacturing.
- I don't want to appear as corporate, just professional

```html
<!DOCTYPE html>
<html lang="en">
<head>
<meta charset="utf-8">
<title>Keystone Advisory Frameworks – Business Cards</title>
<link href="https://fonts.googleapis.com/css2?family=Didact+Gothic&family=Open+Sans:wght@400;600&display=swap" rel="stylesheet">
<style>
  :root {
    --bg: #d9d9d9;
    --card-black: #0a0a0a;
    --brand-red: #e8202a;
    --swoosh-grey: #a6a6a6;
    --text-white: #ffffff;
  }
  * { margin: 0; padding: 0; box-sizing: border-box; }
  html, body {
    width: 1200px; height: 900px; overflow: hidden;
    background: var(--bg);
  }
  .canvas { position: relative; width: 1200px; height: 900px; }
  .card {
    position: absolute; width: 560px; height: 320px;
    overflow: hidden; background: var(--card-black);
  }
  .card--front { left: 320px; top: 110px; }
  .card--back { left: 320px; top: 470px; }

  /* Brand lockup: plain ring + name, one colour, one weight */
  .brand {
    display: flex; flex-direction: column; align-items: center;
    gap: 12px; text-align: center;
  }
  .brand__ring {
    border: 6px solid var(--brand-red); border-radius: 50%;
  }
  .brand__name {
    font-family: "Didact Gothic", sans-serif;
    color: var(--brand-red); text-transform: uppercase;
    letter-spacing: 2px; line-height: 1.15;
  }

  .card--front .brand {
    position: absolute; inset: 0; justify-content: center;
  }
  .card--front .brand__ring { width: 46px; height: 46px; }
  .card--front .brand__name { font-size: 34px; }

  /* Back */
  .back-shapes { position: absolute; inset: 0; }
  .card--back .brand {
    position: absolute; left: 30px; top: 0; width: 240px; height: 320px;
    justify-content: center;
  }
  .card--back .brand__ring { width: 86px; height: 86px; border-width: 8px; }
  .card--back .brand__name { font-size: 21px; letter-spacing: 1.5px; }

  .contact {
    position: absolute; right: 26px; top: 32px;
    font-family: "Open Sans", sans-serif; color: var(--text-white);
    text-align: right;
  }
  .contact__name { font-size: 19px; font-weight: 600; line-height: 1.2; }
  .contact__role { font-size: 14.5px; margin-bottom: 22px; }
  .contact__list { list-style: none; font-size: 14.5px; line-height: 1.5; }
  .contact__list li {
    display: flex; align-items: center; justify-content: flex-end; gap: 8px;
  }
  .contact__list li.contact__address--first { margin-top: 8px; }
  .contact__list svg { width: 13px; height: 13px; flex: none; }
  .contact__spacer { width: 13px; flex: none; }
</style>
</head>
<body>
<main class="canvas">

  <section class="card card--front" aria-label="Card front">
    <div class="brand">
      <span class="brand__ring"></span>
      <div class="brand__name">Keystone Advisory<br>Frameworks</div>
    </div>
  </section>

  <section class="card card--back" aria-label="Card back">
    <svg class="back-shapes" viewBox="0 0 560 320" preserveAspectRatio="none">
      <rect width="560" height="320" fill="var(--card-black)"/>
      <path d="M292 0 C345 70 340 220 200 320 L560 320 L560 0 Z" fill="var(--swoosh-grey)"/>
      <path d="M305 0 C358 72 352 225 218 320 L560 320 L560 0 Z" fill="var(--card-black)"/>
      <path d="M318 0 C370 75 362 230 232 320 L560 320 L560 0 Z" fill="var(--brand-red)"/>
    </svg>

    <div class="brand">
      <span class="brand__ring"></span>
      <div class="brand__name">Keystone<br>Advisory<br>Frameworks</div>
    </div>

    <div class="contact">
      <div class="contact__name">Daniel Hart</div>
      <div class="contact__role">Managing Director</div>
      <ul class="contact__list">
        <li>123.456.7890
          <svg viewBox="0 0 16 16" fill="#fff"><path d="M3 6c0-2 2-3 5-3s5 1 5 3v1h-3V6H6v1H3z"/><rect x="3" y="8" width="10" height="6" rx="1"/></svg>
        </li>
        <li>123.456.7890
          <svg viewBox="0 0 16 16" fill="#fff"><rect x="4" y="1" width="8" height="5"/><rect x="2" y="6" width="12" height="9" rx="1"/></svg>
        </li>
        <li>info@youremail.com
          <svg viewBox="0 0 16 16"><rect x="1" y="3" width="14" height="10" fill="#fff"/><path d="M1 3l7 6 7-6" fill="none" stroke="var(--brand-red)" stroke-width="1.3"/></svg>
        </li>
        <li>www.website.com
          <svg viewBox="0 0 16 16" fill="none" stroke="#fff" stroke-width="2"><rect x="1" y="6" width="8" height="4" rx="2" transform="rotate(-45 5 8)"/><rect x="7" y="6" width="8" height="4" rx="2" transform="rotate(-45 11 8)"/></svg>
        </li>
        <li class="contact__address--first">1234, Address Goes Here
          <svg viewBox="0 0 16 16" fill="#fff"><path d="M8 1a5 5 0 0 1 5 5c0 4-5 9-5 9S3 10 3 6a5 5 0 0 1 5-5z"/><circle cx="8" cy="6" r="2" fill="var(--brand-red)"/></svg>
        </li>
        <li>Country Name, 123456 <span class="contact__spacer"></span></li>
      </ul>
    </div>
  </section>

</main>
</body>
</html>
```